Website for Life Strategies business

We need a website to present our video, audio and print content to subcribers at Bright Summit Mentors. We will offer a team of coaches who can help people breakthrough the barriers that keep them from reaching their physical, spiritual, financial, leadership and relationship goals.

Target Market(s)

Anyone who needs help with strategies to take their life to a new level of success.

Industry/Entity Type

Life Coaching

Logo Text

Bright Summit Mentors

Number of Pages Required

5+ page

Colors

Designer to choose colors to be used in the design.

Requirements
Must have
• The ability to present content as a package that includes Word Documents, videos and audio content as well as to be able to display books for sale. Each week their would be a new package for subscribers to access. It should provide the ability for subscribers to comment on the material and share how their lives were changed by the content. Should also include a shop page to offer merchandise for sale.
Nice to have
• Not sure
Should not have
• Not sure

```html
<!DOCTYPE html>
<html lang="en">
<head>
<meta charset="utf-8">
<title>Bright Summit Mentors</title>
<link href="https://fonts.googleapis.com/css2?family=Roboto+Condensed:wght@400;700&family=Open+Sans:ital,wght@0,400;0,600;1,400;1,600&display=swap" rel="stylesheet">
<style>
  :root {
    --orange: #fb8200;
    --orange-deep: #f07800;
    --ink: #222222;
    --text: #555555;
    --muted: #888888;
    --line: #e2e2e2;
    --white: #ffffff;
    --night: #121820;
    --night-soft: #2a3038;
  }
  * { box-sizing: border-box; margin: 0; padding: 0; }
  html, body { width: 1200px; height: 2442px; overflow: hidden; background: var(--white); }
  body { position: relative; font-family: "Open Sans", Arial, sans-serif; color: var(--text); }
  .abs { position: absolute; }
  .cond { font-family: "Roboto Condensed", "Arial Narrow", sans-serif; }

  /* Hero */
  .hero { left: 0; top: 0; width: 1200px; height: 600px;
    background: linear-gradient(90deg, #f3f3f3 0%, #ececec 45%, #e4e4e4 70%, #d8d8d8 100%); }
  .hero-photo { left: 640px; top: 0; width: 560px; height: 600px;
    background: linear-gradient(160deg, #ececec 0%, #e0ddda 35%, #c9c6c3 70%, #d9d9d9 100%); }
  .top-rule { left: 0; top: 0; width: 1200px; height: 3px; background: var(--orange); }
  .header { left: 0; top: 3px; width: 1200px; height: 84px; background: rgba(255,255,255,.9); }
  .brand { left: 130px; top: 28px; font-size: 28px; font-weight: 700; color: var(--orange); letter-spacing: .2px; }
  .nav { left: 554px; top: 36px; display: flex; gap: 26px; font-size: 13px; color: var(--ink); font-family: "Roboto Condensed", sans-serif; }
  .nav .active { color: var(--orange); }
  .search { left: 1054px; top: 35px; }
  .hero-title { left: 128px; top: 188px; font-size: 66px; font-weight: 700; color: var(--ink); line-height: 1; text-shadow: 2px 3px 4px rgba(0,0,0,.25); }
  .hero-copy { left: 130px; top: 272px; width: 440px; font-size: 19px; line-height: 31px; color: #555; }
  .btn { background: var(--orange); color: var(--white); border-radius: 20px; text-align: center; font-family: "Roboto Condensed", sans-serif; font-size: 11px; text-transform: uppercase; }
  .hero-btn { left: 130px; top: 393px; width: 131px; height: 39px; line-height: 39px; }
  .dots { left: 571px; top: 547px; display: flex; gap: 13px; }
  .dots span { width: 10px; height: 10px; border-radius: 50%; background: #b8b8b8; }
  .dots span:first-child { background: var(--orange); }

  /* Welcome */
  .welcome-title { left: 0; top: 645px; width: 1200px; text-align: center; font-size: 30px; color: var(--ink); }
  .welcome-copy { left: 195px; top: 697px; width: 810px; text-align: center; font-size: 11.5px; line-height: 22px; color: #555; }
  .card { top: 795px; width: 287px; height: 346px; background: var(--white); box-shadow: 0 1px 6px rgba(0,0,0,.22); }
  .card-media { position: absolute; left: 0; top: 0; width: 287px; height: 190px; }
  .card-caption { position: absolute; left: 16px; top: 152px; font-size: 14px; font-weight: 700; color: var(--white); font-family: "Open Sans", sans-serif; letter-spacing: .2px; }
  .card-icon { position: absolute; right: 16px; top: 145px; }
  .card-text { position: absolute; left: 16px; top: 207px; width: 258px; font-size: 11.5px; line-height: 22px; color: #555; }
  .card-btn { position: absolute; left: 16px; top: 287px; width: 98px; height: 39px; line-height: 39px; }

  /* What we do */
  .services { left: 0; top: 1201px; width: 1200px; height: 589px;
    background: radial-gradient(ellipse at 50% 30%, #3a3a40 0%, #23262c 40%, #12161c 80%), var(--night); }
  .services-title { left: 0; top: 1253px; width: 1200px; text-align: center; font-size: 30px; color: var(--white); }
  .service-label { width: 240px; text-align: center; color: var(--white); }
  .service-label h3 { font-family: "Roboto Condensed", sans-serif; font-weight: 400; font-size: 18px; margin-bottom: 6px; }
  .service-label p { font-size: 11.5px; line-height: 19px; }

  /* Testimonials */
  .testi-title { left: 0; top: 1840px; width: 1200px; text-align: center; font-size: 30px; color: var(--ink); }
  .testi-photo { left: 164px; top: 1885px; width: 138px; height: 138px; border-radius: 50%;
    background: linear-gradient(160deg, #d9cfc6, #b49a86 60%, #8f8c8c); border: 4px solid #e8e8e8; }
  .testi-rule { left: 333px; top: 1888px; width: 2px; height: 128px; background: #dcdcdc; }
  .quote { left: 362px; top: 1900px; width: 690px; font-size: 14px; line-height: 24px; font-style: italic; font-weight: 600; color: #555; }
  .quote-author { left: 366px; top: 1985px; font-size: 15px; color: var(--orange); }
  .testi-arrows { left: 1026px; top: 1849px; }

  /* Newsletter */
  .newsletter { left: 0; top: 2083px; width: 1200px; height: 95px; background: var(--orange); overflow: hidden; }
  .news-title { left: 251px; top: 2112px; font-size: 27px; color: var(--white); }
  .news-input { left: 506px; top: 2111px; width: 417px; height: 41px; border-radius: 21px; background: var(--white); font-size: 11px; color: #555; padding: 13px 20px; }
  .news-btn { left: 930px; top: 2111px; width: 138px; height: 41px; line-height: 37px; border: 2px solid var(--white); border-radius: 21px; color: var(--white); text-align: center; font-size: 13px; font-weight: 700; }

  /* Footer */
  .foot-col h4 { font-family: "Roboto Condensed", sans-serif; font-size: 15px; color: var(--ink); font-weight: 700; margin-bottom: 12px; }
  .foot-col li { list-style: none; font-size: 11.5px; line-height: 21px; color: #555; }
  .foot-divider { top: 2208px; width: 1px; height: 146px; background: var(--line); }
  .contact li { display: flex; gap: 12px; align-items: flex-start; }
  .contact svg { flex: none; margin-top: 4px; }
  .social li { display: flex; align-items: center; gap: 14px; margin-bottom: 10px; line-height: 1; }
  .social .dot { width: 24px; height: 24px; border-radius: 50%; background: #555; }
  .foot-rule { left: 130px; top: 2384px; width: 938px; height: 1px; background: var(--line); }
  .copyright { left: 0; top: 2405px; width: 1200px; text-align: center; font-size: 11.5px; color: #555; }
</style>
</head>
<body>

<!-- Hero -->
<div class="abs hero"></div>
<div class="abs hero-photo" role="img" aria-label="Photo of a father sitting against a white brick wall while his young daughter reaches up"></div>
<div class="abs header"></div>
<div class="abs top-rule"></div>
<div class="abs brand cond">BRIGHT SUMMIT MENTORS</div>
<nav class="abs nav">
  <span class="active">HOME</span><span>ABOUT US</span><span>WHAT WE DO</span><span>TESTIMONIALS</span><span>BLOG</span><span>CONTACT US</span>
</nav>
<svg class="abs search" width="14" height="14" viewBox="0 0 14 14" aria-hidden="true"><circle cx="6" cy="6" r="4.5" fill="none" stroke="#333" stroke-width="1.5"/><line x1="9.3" y1="9.3" x2="13" y2="13" stroke="#333" stroke-width="1.5"/></svg>

<h1 class="abs hero-title cond">Lifestyle Strategy</h1>
<p class="abs hero-copy">Lorem ipsum dolor sit amet, consectetur adipiscing Nunc sit amet ex orci. Phasellus elit dui, tempor ut tempus ac, egestas interdum...</p>
<div class="abs btn hero-btn">Learn more info</div>
<div class="abs dots"><span></span><span></span><span></span></div>

<!-- Welcome -->
<h2 class="abs welcome-title cond">Welcome to Bright Summit Mentors</h2>
<p class="abs welcome-copy">Lorem ipsum dolor sit amet, consectetur adipiscing elit. Nunc sit amet ex orci. Phasellus elit dui, tempor ut tempus ac, egestas interdum mauris. In gravida viverra eros et dictum. Maecenas non interdum nisl. Phasellus ultrices id metus quis tempus. Fusce eu iaculis felis. Nam auctor tellus libero, at sagittis lorem iaculis non.Maecenas enim tellus, vulputate non ante eu, pretium tempus lorem</p>

<article class="abs card" style="left:130px">
  <div class="card-media" role="img" aria-label="Photo of a young couple walking in a city street" style="background:linear-gradient(180deg,#8a6a52,#5a4a40 60%,#2a2420)"></div>
  <div class="card-caption">PHASELLUS ULTRICES</div>
  <svg class="card-icon" width="28" height="28" viewBox="0 0 28 28" aria-hidden="true"><circle cx="14" cy="14" r="12" fill="none" stroke="#fff" stroke-width="2.5"/><path d="M11 8.5 L19.5 14 L11 19.5Z" fill="#fff"/></svg>
  <p class="card-text">Vulputate non ante eu, pretium Aliquam id libero ut velit fringilla consectetur. Aliquam erat volutpat. Integer sit amet...</p>
  <div class="btn card-btn">Subscribe</div>
</article>
<article class="abs card" style="left:457px">
  <div class="card-media" role="img" aria-label="Photo of a man jogging outdoors in warm light" style="background:linear-gradient(180deg,#f0d9a8,#d8a060 55%,#5a4030)"></div>
  <div class="card-caption">PHASELLUS ULTRICES</div>
  <svg class="card-icon" width="28" height="28" viewBox="0 0 28 28" aria-hidden="true"><circle cx="14" cy="14" r="12" fill="none" stroke="#fff" stroke-width="2.5"/><path d="M11 8.5 L19.5 14 L11 19.5Z" fill="#fff"/></svg>
  <p class="card-text">Vulputate non ante eu, pretium Aliquam id libero ut velit fringilla consectetur. Aliquam erat volutpat. Integer sit amet...</p>
  <div class="btn card-btn">Subscribe</div>
</article>
<article class="abs card" style="left:783px">
  <div class="card-media" role="img" aria-label="Photo of a laughing couple outdoors in autumn" style="background:linear-gradient(180deg,#c89060,#7a5a48 55%,#2e2622)"></div>
  <div class="card-caption">PHASELLUS ULTRICES</div>
  <svg class="card-icon" width="30" height="28" viewBox="0 0 30 28" aria-hidden="true"><path d="M3 10h5l7-6v20l-7-6H3z" fill="#fff"/><path d="M19 9a7 7 0 0 1 0 10M22.5 6a11 11 0 0 1 0 16" fill="none" stroke="#fff" stroke-width="2"/></svg>
  <p class="card-text">Vulputate non ante eu, pretium Aliquam id libero ut velit fringilla consectetur. Aliquam erat volutpat. Integer sit amet...</p>
  <div class="btn card-btn">Subscribe</div>
</article>

<!-- What we do -->
<section class="abs services" role="img" aria-label="Dark mountain landscape background"></section>
<h2 class="abs services-title cond">What We Do ?</h2>
<svg class="abs" style="left:0;top:1201px" width="1200" height="589" viewBox="0 1201 1200 589" aria-hidden="true">
  <g stroke="#555" stroke-width="1.5" fill="#666">
    <line x1="250" y1="1420" x2="357" y2="1547"/>
    <line x1="447" y1="1547" x2="554" y2="1420"/>
    <line x1="644" y1="1420" x2="751" y2="1547"/>
    <line x1="841" y1="1547" x2="948" y2="1420"/>
    <circle cx="278" cy="1437" r="5"/><circle cx="329" cy="1505" r="5"/>
    <circle cx="474" cy="1505" r="5"/><circle cx="526" cy="1437" r="5"/>
    <circle cx="672" cy="1437" r="5"/><circle cx="723" cy="1505" r="5"/>
    <circle cx="868" cy="1505" r="5"/><circle cx="920" cy="1437" r="5"/>
  </g>
  <g fill="#101214" stroke="#4a4a4a" stroke-width="6">
    <circle cx="205" cy="1388" r="58"/><circle cx="599" cy="1388" r="58"/><circle cx="993" cy="1388" r="58"/>
    <circle cx="402" cy="1579" r="58"/><circle cx="796" cy="1579" r="58"/>
  </g>
  <!-- feet -->
  <g fill="#fff">
    <ellipse cx="192" cy="1392" rx="8" ry="17"/><ellipse cx="218" cy="1398" rx="8" ry="17"/>
    <circle cx="188" cy="1369" r="2.5"/><circle cx="194" cy="1368" r="2.5"/><circle cx="199" cy="1370" r="2"/>
    <circle cx="222" cy="1375" r="2.5"/><circle cx="216" cy="1374" r="2.5"/><circle cx="211" cy="1376" r="2"/>
  </g>
  <!-- presentation board -->
  <g fill="none" stroke="#fff" stroke-width="3">
    <rect x="577" y="1367" width="44" height="30"/><line x1="574" y1="1367" x2="624" y2="1367"/>
    <line x1="599" y1="1397" x2="599" y2="1412"/><line x1="599" y1="1405" x2="588" y2="1414"/><line x1="599" y1="1405" x2="610" y2="1414"/>
    <circle cx="599" cy="1382" r="8"/><path d="M599 1374v8h8"/>
  </g>
  <!-- target -->
  <g fill="none" stroke="#fff" stroke-width="4">
    <circle cx="989" cy="1392" r="24"/><circle cx="989" cy="1392" r="14"/>
  </g>
  <circle cx="989" cy="1392" r="5" fill="#fff"/>
  <path d="M989 1392 L1012 1369 M1006 1367 L1014 1367 L1014 1375" stroke="#fff" stroke-width="3" fill="none"/>
  <!-- wheel -->
  <g fill="none" stroke="#fff" stroke-width="3">
    <circle cx="402" cy="1579" r="18"/><circle cx="402" cy="1579" r="6"/>
    <path d="M402 1551v56M374 1579h56M382 1559l40 40M422 1559l-40 40"/>
  </g>
  <!-- crown -->
  <path d="M770 1568 L781 1580 L796 1560 L811 1580 L822 1568 L818 1594 L774 1594Z" fill="#fff"/>
  <rect x="774" y="1598" width="44" height="5" fill="#fff"/>
</svg>
<div class="abs service-label" style="left:85px;top:1462px"><h3>Physical</h3><p>Lorem ipsum dolor sit amet,<br>consectetur elit...</p></div>
<div class="abs service-label" style="left:479px;top:1462px"><h3>Financial</h3><p>Lorem ipsum dolor sit amet,<br>consectetur elit...</p></div>
<div class="abs service-label" style="left:873px;top:1462px"><h3>Leadership Goals</h3><p>Lorem ipsum dolor sit amet,<br>consectetur elit...</p></div>
<div class="abs service-label" style="left:282px;top:1654px"><h3>Spiritual</h3><p>Lorem ipsum dolor sit amet,<br>consectetur elit...</p></div>
<div class="abs service-label" style="left:676px;top:1654px"><h3>Leadership</h3><p>Lorem ipsum dolor sit amet,<br>consectetur elit...</p></div>

<!-- Testimonials -->
<h2 class="abs testi-title cond">Testimonials</h2>
<svg class="abs testi-arrows" width="44" height="20" viewBox="0 0 44 20" aria-hidden="true">
  <circle cx="8" cy="10" r="7" fill="none" stroke="#bbb" stroke-width="1.5"/><path d="M11 10H5M7.5 7.5L5 10l2.5 2.5" stroke="#bbb" stroke-width="1.5" fill="none"/>
  <circle cx="33" cy="10" r="7" fill="none" stroke="#333" stroke-width="1.5"/><path d="M30 10h6M33.5 7.5L36 10l-2.5 2.5" stroke="#333" stroke-width="1.5" fill="none"/>
</svg>
<div class="abs testi-photo" role="img" aria-label="Portrait of a smiling client"></div>
<div class="abs testi-rule"></div>
<p class="abs quote">“Lorem ipsum dolor sit amet, consectetur adipiscing elit. Nunc sit amet ex orci. Phasellus elit dui, tempor ut tempus ac, egestas interdum mauris. In gravida viverra eros et dictum. Maecenas non interdum Phasellus ultrices id metus quis tempus. Fusce eu iaculis felis. Nam auctor tellus libero...</p>
<div class="abs quote-author cond">-JOHN DOE</div>

<!-- Newsletter -->
<div class="abs newsletter">
  <svg style="position:absolute;left:128px;top:12px" width="110" height="95" viewBox="0 0 110 95" aria-hidden="true">
    <g fill="#e06f00" transform="rotate(-18 55 55)">
      <rect x="10" y="30" width="90" height="60"/>
      <path d="M10 30 L55 62 L100 30Z" fill="#d86a00"/>
    </g>
  </svg>
</div>
<div class="abs news-title cond">Subscribe Newsletter :</div>
<div class="abs news-input">Enter Your Email Id :</div>
<div class="abs news-btn cond">SUBSCRIBE</div>

<!-- Footer -->
<div class="abs foot-col" style="left:130px;top:2208px">
  <h4>QUICK LINKS</h4>
  <ul><li>Home</li><li>About Us</li><li>What we do</li><li>Testimonials</li><li>Blog</li><li>Contact Us</li></ul>
</div>
<div class="abs foot-divider" style="left:278px"></div>
<div class="abs foot-col" style="left:352px;top:2208px">
  <h4>INFORMATION</h4>
  <ul><li>Terms &amp; Conditions</li><li>Privacy Policy</li><li>Disclaimer</li><li>Site Map</li></ul>
</div>
<div class="abs foot-divider" style="left:526px"></div>
<div class="abs foot-col contact" style="left:599px;top:2208px;width:200px">
  <h4>CONTACT INFO</h4>
  <ul>
    <li><svg width="12" height="12" viewBox="0 0 12 12"><path d="M1 3c0-1 1-2 2-2h6c1 0 2 1 2 2v1H8V3H4v1H1z M2 6h8l1 5H1z" fill="#555"/></svg>(555) 014-2290</li>
    <li><svg width="12" height="12" viewBox="0 0 12 12"><rect x="3" y="1" width="6" height="3" fill="#555"/><rect x="1" y="4" width="10" height="5" fill="#555"/><rect x="3" y="8" width="6" height="3" fill="#888"/></svg>(555) 014-2290</li>
    <li><svg width="12" height="10" viewBox="0 0 12 10"><rect x="0.5" y="0.5" width="11" height="9" fill="none" stroke="#555"/><path d="M0.5 0.5L6 5.5 11.5 0.5" fill="none" stroke="#555"/></svg><span style="text-decoration:underline">info@yourmailid.com</span></li>
    <li style="line-height:17px;margin-top:4px"><svg width="10" height="13" viewBox="0 0 10 13"><path d="M5 13C5 13 0 7.5 0 5a5 5 0 0 1 10 0c0 2.5-5 8-5 8z" fill="#555"/><circle cx="5" cy="5" r="1.8" fill="#fff"/></svg>#2868 Lorem ipsum dolor sit amet, consectetur</li>
  </ul>
</div>
<div class="abs foot-divider" style="left:843px"></div>
<div class="abs foot-col social" style="left:915px;top:2208px">
  <h4>OUR SOCIAL NETWORKS</h4>
  <ul>
    <li><span class="dot"></span>Friendnet</li>
    <li><span class="dot"></span>Chirpline</li>
    <li><span class="dot"></span>Circlesphere</li>
    <li><span class="dot"></span>Workweave</li>
  </ul>
</div>
<div class="abs foot-rule"></div>
<div class="abs copyright">Copyrights © Bright Summit Mentors . 2017 | Allrights Reserved</div>

</body>
</html>
```